Harborline Auto LLC

Car Dealer Customer Service
Address: 2874 Cresthaven Road, Shelbyville, TN 37162
web: www.harborlineautoxq.net
email: harborlineautoxq@mailnest.example
Phone: (931) 555-0148
Phone: (629) 555-0173

```html
<!DOCTYPE html>
<html lang="en">
<head>
<meta charset="utf-8">
<title>Harborline Auto – Business Card</title>
<link rel="stylesheet" href="https://fonts.googleapis.com/css2?family=Jost:wght@400;500;700&family=Montserrat:wght@700;800&display=swap">
<style>
  :root {
    --backdrop: #e4e7e6;
    --brand-blue: #2a92cf;
    --brand-navy: #1d6aa8;
    --brand-gold: #eba93a;
    --paper: #ffffff;
  }
  * { box-sizing: border-box; margin: 0; padding: 0; }
  html, body { width: 1200px; height: 900px; overflow: hidden; }
  body {
    background: var(--backdrop);
    font-family: "Jost", sans-serif;
    position: relative;
  }
  .card {
    position: absolute;
    left: 250px;
    width: 700px;
    height: 400px;
    overflow: hidden;
    box-shadow: 0 6px 18px rgba(0,0,0,0.12);
  }
  .card--front { top: 35px; background: var(--brand-blue); }
  .card--back  { top: 465px; background: var(--brand-blue); }

  /* Front */
  .front__top {
    position: absolute; inset: 0 0 auto 0;
    height: 150px;
    background: var(--paper);
  }
  .wordmark {
    position: absolute;
    display: flex; align-items: center; gap: 14px;
    white-space: nowrap;
  }
  .wordmark__dot { border-radius: 50%; flex: none; }
  .front__mark {
    left: 50%; top: 122px; transform: translateX(-50%);
  }
  .front__mark .wordmark__dot { width: 52px; height: 52px; background: var(--brand-gold); }
  .front__mark .wordmark__name {
    font-family: "Montserrat", sans-serif; font-weight: 800;
    font-size: 30px; letter-spacing: 1px; color: var(--brand-navy);
    line-height: 1;
  }
  .front__mark .wordmark__name { background: var(--paper); padding: 4px 6px; }

  .person {
    position: absolute; left: 60px; bottom: 62px;
    color: var(--paper);
  }
  .person__name { font-size: 26px; font-weight: 400; letter-spacing: 1px; }
  .person__name strong { font-weight: 700; }
  .person__role { font-size: 16px; margin-top: 2px; }

  .contacts {
    position: absolute; left: 375px; top: 205px;
    list-style: none; color: var(--paper);
    font-size: 12.5px; line-height: 1.3;
  }
  .contacts li { display: flex; align-items: center; gap: 10px; margin-bottom: 8px; }
  .contacts svg { width: 13px; height: 13px; flex: none; }

  /* Back */
  .back__lockup {
    position: absolute; left: 50%; top: 50%;
    transform: translate(-50%, -50%);
    display: flex; flex-direction: column; align-items: center;
  }
  .back__mark { position: static; }
  .back__mark .wordmark__dot { width: 70px; height: 70px; background: var(--paper); }
  .back__mark .wordmark__name {
    font-family: "Montserrat", sans-serif; font-weight: 800;
    font-size: 40px; letter-spacing: 1px; color: var(--paper);
  }
  .back__tagline {
    margin-top: 10px; color: var(--paper);
    font-family: "Montserrat", sans-serif; font-weight: 700;
    font-size: 14px; letter-spacing: 1px;
  }
</style>
</head>
<body>

<section class="card card--front" aria-label="Business card front">
  <div class="front__top"></div>
  <div class="wordmark front__mark">
    <span class="wordmark__dot"></span>
    <span class="wordmark__name">HARBORLINE AUTO</span>
  </div>

  <div class="person">
    <p class="person__name">PERSON <strong>NAME</strong></p>
    <p class="person__role">Chief Executive</p>
  </div>

  <ul class="contacts">
    <li>
      <svg viewBox="0 0 16 16" fill="none" stroke="#fff" stroke-width="1.6"><path d="M3 2h3l1.5 3.5-2 1.2a8 8 0 0 0 3.8 3.8l1.2-2L14 10v3a1 1 0 0 1-1 1A11 11 0 0 1 2 3a1 1 0 0 1 1-1z"/></svg>
      (931) 555-0148, (629) 555-0173
    </li>
    <li>
      <svg viewBox="0 0 16 16" fill="none" stroke="#fff" stroke-width="1.4"><circle cx="8" cy="8" r="6.3"/><path d="M1.7 8h12.6M8 1.7c2.2 2 2.2 10.6 0 12.6M8 1.7c-2.2 2-2.2 10.6 0 12.6"/></svg>
      www.harborlineautoxq.net
    </li>
    <li>
      <svg viewBox="0 0 16 16" fill="none" stroke="#fff" stroke-width="1.4"><rect x="1.5" y="3.5" width="13" height="9" rx="1"/><path d="M1.5 4l6.5 5 6.5-5"/></svg>
      harborlineautoxq@mailnest.example
    </li>
    <li>
      <svg viewBox="0 0 16 16" fill="none" stroke="#fff" stroke-width="1.5"><path d="M8 15s5-5.2 5-8.8A5 5 0 0 0 3 6.2C3 9.8 8 15 8 15z"/><circle cx="8" cy="6.3" r="1.8"/></svg>
      2874 Cresthaven Road, Shelbyville, TN 37162
    </li>
  </ul>
</section>

<section class="card card--back" aria-label="Business card back">
  <div class="back__lockup">
    <div class="wordmark back__mark">
      <span class="wordmark__dot"></span>
      <span class="wordmark__name">HARBORLINE AUTO</span>
    </div>
    <p class="back__tagline">CAR DEALER CUSTOMER SERVICE</p>
  </div>
</section>

</body>
</html>
```